Business Card Design

I already have a company logo for my company. I have a logo for the manufacturer we represent. I want a professional business card design.

```html
<!DOCTYPE html>
<html lang="en">
<head>
<meta charset="utf-8">
<title>Business Card – Front and Back</title>
<link rel="stylesheet" href="https://fonts.googleapis.com/css2?family=Lato:wght@400;700&family=Russo+One&display=swap">
<style>
  :root {
    --page: #d9d9db;
    --card-top: #262626;
    --card-bottom: #161616;
    --edge-gold: #e0a800;
    --accent-red: #e8202a;
    --accent-gold: #e6a317;
    --text-light: #f2f2f2;
    --rule-silver: #c9c9c9;
  }
  * { box-sizing: border-box; margin: 0; padding: 0; }
  html, body { width: 1200px; height: 982px; overflow: hidden; }
  body {
    background: var(--page);
    font-family: "Lato", sans-serif;
    position: relative;
  }
  .card {
    position: absolute;
    left: 220px;
    width: 760px;
    height: 434px;
    border-radius: 26px;
    background: linear-gradient(160deg, var(--card-top), var(--card-bottom));
    border: 3px solid var(--edge-gold);
    box-shadow: 0 10px 24px rgba(0,0,0,.25);
    overflow: hidden;
  }
  .card--front { top: 40px; }
  .card--back { top: 508px; }

  .brand {
    display: flex;
    align-items: center;
    gap: 14px;
    font-family: "Lato", sans-serif;
    font-weight: 700;
    color: var(--text-light);
    letter-spacing: 1px;
    text-transform: uppercase;
  }
  .brand__mark {
    background: var(--accent-red);
    flex: none;
  }
  .card--front .brand {
    position: absolute;
    left: 50%; top: 50%;
    transform: translate(-50%, -50%);
    font-size: 44px;
    white-space: nowrap;
  }
  .card--front .brand__mark { width: 40px; height: 40px; }

  .person {
    position: absolute;
    left: 52px; top: 52px;
  }
  .person__name {
    font-family: "Russo One", sans-serif;
    color: var(--accent-red);
    font-size: 40px;
    letter-spacing: 3px;
    line-height: 1;
  }
  .person__role {
    color: var(--accent-gold);
    font-size: 20px;
    margin-top: 8px;
  }
  .divider {
    position: absolute;
    height: 2px;
    background: linear-gradient(90deg, rgba(201,201,201,0), var(--rule-silver) 30%, var(--rule-silver) 70%, rgba(201,201,201,0));
  }
  .divider--left { left: 52px; top: 148px; width: 400px; }
  .divider--right { right: 52px; top: 288px; width: 300px; }

  .contact {
    position: absolute;
    left: 52px; top: 172px;
    list-style: none;
  }
  .contact__item {
    display: flex;
    align-items: center;
    gap: 14px;
    color: var(--text-light);
    font-size: 22px;
    line-height: 40px;
  }
  .contact__icon { width: 18px; height: 18px; fill: var(--accent-red); flex: none; }

  .card--back .brand {
    position: absolute;
    right: 52px; top: 110px;
    font-size: 30px;
  }
  .card--back .brand__mark { width: 28px; height: 28px; }

  .company {
    position: absolute;
    right: 52px; top: 304px;
    text-align: right;
    color: var(--text-light);
    font-size: 19px;
    line-height: 26px;
  }
  .company__name { color: var(--accent-red); }
</style>
</head>
<body>

<section class="card card--front">
  <div class="brand"><span class="brand__mark"></span>Beacon Alert Group</div>
</section>

<section class="card card--back">
  <div class="person">
    <h1 class="person__name">JOHN SMITH</h1>
    <p class="person__role">Founder &amp; CEO</p>
  </div>
  <div class="divider divider--left"></div>

  <ul class="contact">
    <li class="contact__item">
      <svg class="contact__icon" viewBox="0 0 24 24"><path d="M6.6 10.8a15 15 0 0 0 6.6 6.6l2.2-2.2c.3-.3.7-.4 1-.2 1.1.4 2.3.6 3.6.6.6 0 1 .4 1 1V20c0 .6-.4 1-1 1A17 17 0 0 1 3 4c0-.6.4-1 1-1h3.5c.6 0 1 .4 1 1 0 1.3.2 2.5.6 3.6.1.3 0 .7-.2 1z"/></svg>
      (123) 456-7890
    </li>
    <li class="contact__item">
      <svg class="contact__icon" viewBox="0 0 24 24"><path d="M7 1h10a2 2 0 0 1 2 2v18a2 2 0 0 1-2 2H7a2 2 0 0 1-2-2V3a2 2 0 0 1 2-2zm0 3v14h10V4zm5 15.5a1 1 0 1 0 0 2 1 1 0 0 0 0-2z"/></svg>
      (123) 456-7890
    </li>
    <li class="contact__item">
      <svg class="contact__icon" viewBox="0 0 24 24"><path d="M6 2h12v5H6zM4 8h16a2 2 0 0 1 2 2v7h-4v5H6v-5H2v-7a2 2 0 0 1 2-2zm4 8v4h8v-4z"/></svg>
      (123) 456-7890
    </li>
    <li class="contact__item">
      <svg class="contact__icon" viewBox="0 0 24 24"><path d="M2 5h20v14H2zm2 2v.5l8 5 8-5V7l-8 5z"/></svg>
      info@yourwebsitehere.com
    </li>
  </ul>

  <div class="brand"><span class="brand__mark"></span>Beacon Alert Group</div>
  <div class="divider divider--right"></div>

  <address class="company" style="font-style: normal;">
    <div class="company__name">Beacon Alert Group</div>
    <div>423 Street Address Here, City</div>
    <div>State &amp; ZIP Code Country</div>
    <div>www.yourwebsitehere.com</div>
  </address>
</section>

</body>
</html>
```